Veltrano.co - Polar Expeditions Specialists

We need a modern, visually striking business card for Veltrano.co, a company specialized in selling expedition cruises to the most remote regions on Earth, with a focus on the Arctic and Antarctica. The design should instantly communicate that the cardholder is an expert in polar travel. Use clean, premium aesthetics with cool tones like icy blue and white, possibly incorporating polar imagery (ice, glaciers, penguins, etc.)

Attached the logo

Contact Information for Business Card

Feels high-end and trustworthy.. Visually memorable — encourages people to keep it

Colors
0054AA
0677BA
7BADD7
CADEEF
E8F1F8

Requirements
Must have
• ice, glaciers, penguins, montains
Nice to have
• modern, transparente,

```html
<!DOCTYPE html>
<html lang="en">
<head>
<meta charset="UTF-8">
<title>Veltrano.co – Business Card</title>
<link href="https://fonts.googleapis.com/css2?family=Poppins:wght@400;500;600;700&display=swap" rel="stylesheet">
<style>
  :root {
    --backdrop: #d3d4d6;
    --brand-blue: #3577b8;
    --photo-deep: #4d6fa6;
    --photo-light: #6f8cbf;
    --ice: #cadeef;
    --white: #ffffff;
    --ink: #1e1e1e;
  }
  * { margin: 0; padding: 0; box-sizing: border-box; }
  html, body {
    width: 900px; height: 1200px; overflow: hidden;
    background: var(--backdrop);
    font-family: "Poppins", sans-serif;
  }
  .card {
    position: absolute;
    box-shadow: 6px 8px 12px rgba(0,0,0,0.35);
    overflow: hidden;
  }
  /* Front */
  .card-front { left: 135px; top: 212px; width: 632px; height: 363px; }
  .front-photo {
    position: absolute; inset: 0;
    background: linear-gradient(160deg, var(--photo-light) 0%, var(--photo-deep) 55%, var(--photo-light) 100%);
  }
  .front-brand {
    position: absolute; left: 0; right: 0; top: 90px;
    text-align: center; color: var(--white);
  }
  .front-mark {
    width: 64px; height: 64px; border-radius: 50%;
    background: var(--white); margin: 0 auto 14px;
  }
  .front-name { font-size: 66px; font-weight: 700; line-height: 1; letter-spacing: -0.5px; }
  .front-tagline { font-size: 21px; font-weight: 600; margin-top: 10px; }

  /* Back */
  .card-back { left: 133px; top: 624px; width: 633px; height: 365px; background: var(--white); }
  .back-name {
    position: absolute; left: 33px; top: 34px;
    color: var(--brand-blue); font-size: 53px; font-weight: 700; line-height: 1; letter-spacing: -0.5px;
  }
  .back-tagline {
    position: absolute; left: 33px; top: 91px;
    color: var(--brand-blue); font-size: 16px; font-weight: 600;
  }
  .holder-name {
    position: absolute; left: 33px; top: 158px;
    color: var(--brand-blue); font-size: 25px; font-weight: 700;
  }
  .holder-role {
    position: absolute; left: 33px; top: 190px;
    color: var(--ink); font-size: 17px; font-weight: 500; letter-spacing: 1px;
  }
  .contact-list { position: absolute; left: 33px; top: 226px; list-style: none; }
  .contact-list li {
    display: flex; align-items: center; height: 25.5px;
    font-size: 15px; color: var(--ink); font-weight: 500; letter-spacing: 1px;
  }
  .contact-list li.phone-number { letter-spacing: 3px; }
  .contact-list svg { width: 14px; height: 14px; margin-right: 8px; fill: var(--brand-blue); flex: none; }
  .back-mark {
    position: absolute; left: 375px; top: 40px;
    width: 250px; height: 250px; border-radius: 50%;
    background: var(--brand-blue);
  }
</style>
</head>
<body>
  <section class="card card-front">
    <div class="front-photo" role="img" aria-label="Blue-toned photo of a penguin on snowy ice in front of a glacier-covered mountain and sea"></div>
    <div class="front-brand">
      <div class="front-mark"></div>
      <div class="front-name">Veltrano.co</div>
      <div class="front-tagline">Polar Expeditions Specialists</div>
    </div>
  </section>

  <section class="card card-back">
    <div class="back-name">Veltrano.co</div>
    <div class="back-tagline">Polar Expeditions Specialists</div>
    <div class="holder-name">Dorian Halvers</div>
    <div class="holder-role">Owner</div>
    <ul class="contact-list">
      <li class="phone-number">
        <svg viewBox="0 0 24 24"><path d="M6.6 10.8a15 15 0 0 0 6.6 6.6l2.2-2.2a1 1 0 0 1 1-.25 11.4 11.4 0 0 0 3.6.57 1 1 0 0 1 1 1V20a1 1 0 0 1-1 1A17 17 0 0 1 3 4a1 1 0 0 1 1-1h3.5a1 1 0 0 1 1 1c0 1.25.2 2.45.57 3.57a1 1 0 0 1-.25 1z"/></svg>
        555-204-7316
      </li>
      <li class="phone-number">
        <svg viewBox="0 0 24 24"><path d="M7 1h10a2 2 0 0 1 2 2v18a2 2 0 0 1-2 2H7a2 2 0 0 1-2-2V3a2 2 0 0 1 2-2zm0 3v14h10V4zm5 15.5a1 1 0 1 0 0 2 1 1 0 0 0 0-2z"/></svg>
        555-618-0942
      </li>
      <li>
        <svg viewBox="0 0 24 24"><path d="M2 5h20v14H2zm2 2v.5l8 5 8-5V7z"/></svg>
        info@Veltrano.co
      </li>
      <li>
        <svg viewBox="0 0 24 24"><path d="M12 2a10 10 0 1 0 0 20 10 10 0 0 0 0-20zm6.9 6h-3a15 15 0 0 0-1.3-3.9A8 8 0 0 1 18.9 8zM12 4c.8 1.1 1.5 2.5 1.9 4h-3.8c.4-1.5 1.1-2.9 1.9-4zM4.3 14a8 8 0 0 1 0-4h3.4a16 16 0 0 0 0 4zm.8 2h3a15 15 0 0 0 1.3 3.9A8 8 0 0 1 5.1 16zm3-8h-3a8 8 0 0 1 4.3-3.9A15 15 0 0 0 8.1 8zM12 20c-.8-1.1-1.5-2.5-1.9-4h3.8c-.4 1.5-1.1 2.9-1.9 4zm2.3-6H9.7a14 14 0 0 1 0-4h4.6a14 14 0 0 1 0 4zm.3 5.9a15 15 0 0 0 1.3-3.9h3a8 8 0 0 1-4.3 3.9zm1.7-5.9a16 16 0 0 0 0-4h3.4a8 8 0 0 1 0 4z"/></svg>
        Veltrano.co
      </li>
    </ul>
    <div class="back-mark"></div>
  </section>
</body>
</html>
```